Marlowe Crest Realty business card design

Looking for an upscale and clean business card design and updated logo. I sell to a very high-end south Florida real estate market.
Target Market(s)
High-end real estate in south Florida real estate market
Industry/Entity Type
Real Estate Agent
Contact Information for Business Card
Marlowe Crest Realty, Inc
738 West Pinecrest Ave, Suite 410/510, Fort Lauderdale, FL 33308
Gary Whitlock - Broker/Owner
954-327-8846 Direct
garyshomes@quellmail.com
Website: DwellTarrowBay.com
Font styles to use
Other font styles liked:
- Copperplate Gothic, Georgia, etc.
Requirements
Must have
- My photo, company name, my name and title, all info stated in Details above
Nice to have
- Luxury home design element, waterfront

```html
<!DOCTYPE html>
<html lang="en">
<head>
<meta charset="utf-8">
<title>Marlowe Crest Realty – Business Card</title>
<link href="https://fonts.googleapis.com/css2?family=Arimo:wght@400;700&family=Cormorant+Garamond:wght@500&display=swap" rel="stylesheet">
<style>
  :root {
    --backdrop: #2b2b2d;
    --card-black: #0b0b0b;
    --card-white: #ffffff;
    --gold: #f3c431;
    --ink: #2e2e2e;
    --ink-soft: #4a4a4a;
    --rule: #555555;
    --photo-top: #c9ccd6;
    --photo-bottom: #2f4f9a;
  }
  * { margin: 0; padding: 0; box-sizing: border-box; }
  html, body { width: 1200px; height: 900px; overflow: hidden; }
  body {
    background: var(--backdrop);
    position: relative;
    font-family: "Arimo", Arial, sans-serif;
  }
  .card {
    position: absolute;
    left: 280px;
    width: 640px;
    height: 366px;
    border-radius: 22px;
    overflow: hidden;
  }
  .card--front { top: 64px; background: var(--card-black); }
  .card--back { top: 470px; background: var(--card-white); }

  .brand {
    position: absolute;
    display: flex;
    align-items: center;
    gap: 14px;
  }
  .brand__dot {
    border-radius: 50%;
    background: var(--gold);
    flex: none;
  }
  .brand__name {
    font-family: "Cormorant Garamond", Georgia, serif;
    font-weight: 500;
    line-height: 1.1;
    white-space: nowrap;
  }
  .card--front .brand { left: 0; right: 0; top: 0; bottom: 0; justify-content: center; }
  .card--front .brand__dot { width: 96px; height: 96px; }
  .card--front .brand__name { color: #ffffff; font-size: 38px; }

  .card--back .brand { right: 36px; top: 52px; }
  .card--back .brand__dot { width: 62px; height: 62px; }
  .card--back .brand__name { color: var(--ink); font-size: 22px; }

  .portrait {
    position: absolute;
    left: 42px; top: 26px;
    width: 132px; height: 132px;
    border-radius: 50%;
    background: linear-gradient(180deg, var(--photo-top) 0%, #b9a9b4 45%, var(--photo-bottom) 100%);
  }
  .agent-name {
    position: absolute; left: 42px; top: 170px;
    font-size: 30px; font-weight: 700; color: var(--gold);
    letter-spacing: 0.5px; white-space: nowrap;
  }
  .agent-title {
    position: absolute; left: 42px; top: 208px;
    font-size: 17px; color: var(--ink-soft);
  }
  .divider {
    position: absolute; left: 42px; right: 36px; top: 238px;
    height: 1px; background: var(--rule);
  }
  .address {
    position: absolute; right: 36px; top: 182px;
    text-align: right; font-size: 15px; line-height: 1.45; color: var(--ink-soft);
    white-space: nowrap;
  }
  .contact {
    position: absolute; left: 42px; top: 250px;
    list-style: none;
  }
  .contact li {
    display: flex; align-items: center; gap: 12px;
    font-size: 17px; color: var(--ink); height: 27px;
    white-space: nowrap;
  }
  .contact svg { width: 18px; height: 18px; flex: none; }
  .band {
    position: absolute; left: 0; right: 0; top: 310px; height: 32px;
    background: var(--gold);
    display: flex; align-items: center; justify-content: center;
  }
  .website { font-size: 17px; color: var(--ink); letter-spacing: 0.5px; }
</style>
</head>
<body>
  <section class="card card--front">
    <div class="brand">
      <span class="brand__dot"></span>
      <span class="brand__name">Marlowe Crest<br>Realty, Inc.</span>
    </div>
  </section>

  <section class="card card--back">
    <div class="brand">
      <span class="brand__dot"></span>
      <span class="brand__name">Marlowe Crest Realty, Inc.</span>
    </div>

    <div class="portrait" role="img" aria-label="Portrait photo of Gary Whitlock"></div>
    <div class="agent-name">Gary Whitlock</div>
    <div class="agent-title">Broker/Owner</div>

    <div class="address">738 West Pinecrest Ave, Suite 410/510<br>Fort Lauderdale, FL 33308</div>
    <div class="divider"></div>

    <ul class="contact">
      <li>
        <svg viewBox="0 0 24 24" aria-hidden="true"><path fill="#f3c431" d="M6.6 10.8a15 15 0 0 0 6.6 6.6l2.2-2.2a1 1 0 0 1 1-.25 11.4 11.4 0 0 0 3.6.57 1 1 0 0 1 1 1V20a1 1 0 0 1-1 1A17 17 0 0 1 3 4a1 1 0 0 1 1-1h3.5a1 1 0 0 1 1 1c0 1.25.2 2.45.57 3.57a1 1 0 0 1-.25 1z"/></svg>
        954-327-8846 Direct
      </li>
      <li>
        <svg viewBox="0 0 24 24" aria-hidden="true"><rect x="2" y="5" width="20" height="14" rx="1" fill="#f3c431"/><path d="M2.5 6l9.5 7 9.5-7" fill="none" stroke="#ffffff" stroke-width="1.6"/></svg>
        garyshomes@quellmail.com
      </li>
    </ul>

    <div class="band"><span class="website">www.DwellTarrowBay.com</span></div>
  </section>
</body>
</html>
```